Business Card for a mobile physiotherapy company

I need a layout for a business card for a mobile physiotherapy company.
Slogan is "Mobile Physiotherapy - Your Road To Recovery"
Phone number is 867-555-0142
Email VardenTherapy@postnest.ca (subject to change with website)
Website www.VardenTherapy.ca
My name and credentials: Luke Varden Luke Varden, BSc(kin), MPT, CAFCI, IMS
Information maybe included: Direct Billing, Services including Physiotherapy, IMS, acupuncture
Maybe include facebook and instagram logos
One side with the logo clean and sharp
Other side with details, try not to look too busy, keep everything concise

```html
<!DOCTYPE html>
<html lang="en">
<head>
<meta charset="utf-8">
<title>Varden Therapy – Business Card</title>
<link href="https://fonts.googleapis.com/css2?family=Libre+Baskerville:wght@700&family=PT+Sans:wght@400;700&display=swap" rel="stylesheet">
<style>
  :root {
    --navy: #2c4870;
    --green: #0d5a4a;
    --ink: #1e1e1e;
    --card: #ffffff;
    --edge: #a9abae;
    --bg-light: #e8e9ea;
    --bg-dark: #b3b4b7;
  }
  * { margin: 0; padding: 0; box-sizing: border-box; }
  html, body { width: 1200px; height: 1114px; overflow: hidden; }
  body {
    position: relative;
    background: linear-gradient(90deg, var(--bg-light), var(--bg-dark));
    font-family: "PT Sans", sans-serif;
    color: var(--ink);
  }
  .card {
    position: absolute;
    width: 768px;
    height: 439px;
    background: var(--card);
    border: 1px solid var(--edge);
    border-radius: 38px;
    overflow: hidden;
  }
  .card-front { left: 361px; top: 98px; }
  .card-back { left: 76px; top: 587px; }

  .name-bar {
    position: absolute; left: 0; top: 61px;
    width: 16px; height: 48px; background: var(--navy);
  }
  .holder-name {
    position: absolute; left: 33px; top: 64px;
    font-family: "Libre Baskerville", serif; font-weight: 700;
    font-size: 25px; letter-spacing: 1px; color: var(--navy);
  }
  .credentials {
    position: absolute; left: 33px; top: 100px; font-size: 16px;
  }
  .contact-list { position: absolute; left: 33px; top: 152px; list-style: none; }
  .contact-list li {
    display: flex; align-items: center; gap: 6px;
    height: 33px; font-size: 19.5px;
  }
  .contact-list svg { width: 20px; height: 20px; flex: none; }
  .services-title {
    position: absolute; left: 33px; top: 276px;
    font-size: 20px; font-weight: 700; color: var(--navy);
  }
  .services-list {
    position: absolute; left: 33px; top: 311px;
    list-style: none; color: var(--green); font-size: 21px;
  }
  .services-row { display: flex; gap: 14px; line-height: 28px; }
  .services-row span::before { content: "• "; font-size: 15px; vertical-align: 3px; }
  .footer-band { position: absolute; left: 0; top: 380px; width: 768px; height: 59px; }
  .slogan {
    position: absolute; left: 34px; top: 384px;
    font-family: "Libre Baskerville", serif; font-weight: 700;
    font-size: 18.5px; color: #fff;
  }

  .brand-name {
    position: absolute;
    display: flex; align-items: center;
    font-family: "PT Sans", sans-serif; font-weight: 700;
    color: var(--navy); white-space: nowrap;
  }
  .brand-square { flex: none; background: var(--navy); }
  .brand-front { right: 40px; top: 92px; font-size: 26px; gap: 10px; }
  .brand-front .brand-square { width: 20px; height: 20px; }
  .brand-back {
    left: 0; top: 170px; width: 100%;
    justify-content: center; font-size: 60px;
  }

  .social-row {
    position: absolute; left: 166px; top: 377px;
    display: flex; align-items: center; font-size: 24px;
  }
  .social-item { display: flex; align-items: center; gap: 11px; }
  .social-item + .social-item { margin-left: 26px; }
  .social-square { width: 48px; height: 48px; border-radius: 4px; background: var(--navy); }
</style>
</head>
<body>
  <section class="card card-front" aria-label="Card front">
    <div class="name-bar"></div>
    <h1 class="holder-name">LUKE VARDEN</h1>
    <p class="credentials">BSc(kin), MPT, CAFCI, IMS</p>

    <ul class="contact-list">
      <li>
        <svg viewBox="0 0 20 20" aria-hidden="true"><circle cx="10" cy="10" r="9" fill="none" stroke="var(--navy)" stroke-width="1.6"/><path d="M6.5 5.5l2 .2.6 2.2-1.2 1a6 6 0 0 0 3.2 3.2l1-1.2 2.2.6.2 2c-4.5.8-8.8-3.5-8-8z" fill="var(--navy)"/></svg>
        867-555-0142
      </li>
      <li>
        <svg viewBox="0 0 20 20" aria-hidden="true"><circle cx="10" cy="10" r="9" fill="none" stroke="var(--navy)" stroke-width="1.6"/><rect x="5.5" y="7" width="9" height="6.5" fill="none" stroke="var(--navy)" stroke-width="1.4"/><path d="M5.5 7l4.5 3.5L14.5 7" fill="none" stroke="var(--navy)" stroke-width="1.4"/></svg>
        VardenTherapy@postnest.ca
      </li>
      <li>
        <svg viewBox="0 0 20 20" aria-hidden="true"><g fill="none" stroke="var(--navy)" stroke-width="1.4"><circle cx="10" cy="10" r="8.5"/><ellipse cx="10" cy="10" rx="3.8" ry="8.5"/><path d="M1.5 10h17M3 5.5h14M3 14.5h14"/></g></svg>
        www.VardenTherapy.ca
      </li>
    </ul>

    <h2 class="services-title">Services Including</h2>
    <div class="services-list">
      <div class="services-row"><span>Physiotherapy</span><span>Direct Billing</span></div>
      <div class="services-row"><span>Ims</span><span>Acupuncture</span></div>
    </div>

    <svg class="footer-band" viewBox="0 0 768 59" aria-hidden="true">
      <rect width="768" height="59" fill="var(--navy)"/>
      <path d="M0 0H540L518 22Q512 32 500 32H0Z" fill="var(--green)"/>
    </svg>
    <p class="slogan">Mobile Physiotherapy - Your Road To Recovery</p>

    <div class="brand-name brand-front">
      <span class="brand-square"></span>Varden Therapy
    </div>
  </section>

  <section class="card card-back" aria-label="Card back">
    <div class="brand-name brand-back">Varden Therapy</div>
    <div class="social-row">
      <div class="social-item"><span class="social-square"></span>VardenTherapy</div>
      <div class="social-item"><span class="social-square"></span>@VardenTherapy</div>
    </div>
  </section>
</body>
</html>
```